Bookkeeping business needs a digital and print flyer

We need a flyer to promote our virtual bookkeeping services to small and mid-sized businesses in the United States. We want the content and design of the flyer to be consistent with our website: www.brightlanebookkeeping.example. We would like both a print version and a digital version of the flyer.

```html
<!DOCTYPE html>
<html lang="en">
<head>
<meta charset="utf-8">
<title>Bright Lane Bookkeeping – Virtual Bookkeeping Flyer</title>
<link href="https://fonts.googleapis.com/css2?family=Bebas+Neue&family=Montserrat:wght@400;600;800&family=Poppins:wght@400;500;600;700&display=swap" rel="stylesheet">
<style>
  :root{
    --ink:#1c1c1c;
    --ink-soft:#2e2e2e;
    --yellow:#fbc92a;
    --yellow-bright:#fdd31c;
    --white:#ffffff;
    --photo-a:#cfdbe3;
    --photo-b:#eef2f5;
    --photo-c:#2b3c52;
  }
  *{margin:0;padding:0;box-sizing:border-box}
  html,body{width:868px;height:1200px;overflow:hidden;background:var(--ink)}
  .flyer{
    position:relative;width:868px;height:1200px;overflow:hidden;
    background:radial-gradient(ellipse at 40% 45%, #333 0%, var(--ink) 65%);
    color:var(--white);font-family:"Poppins",sans-serif;
  }
  .abs{position:absolute}

  /* brand */
  .brand{left:50px;top:52px;display:flex;align-items:center;gap:12px}
  .brand-name{font-family:"Montserrat",sans-serif;font-weight:400;font-size:24px;line-height:1.05;letter-spacing:1px;color:var(--white)}
  .brand-mark{width:40px;height:40px;border:2px solid var(--white);border-radius:50%}

  /* headline */
  .headline{left:50px;top:146px;font-family:"Montserrat",sans-serif;font-weight:800;text-transform:uppercase}
  .headline .light{display:block;font-weight:600;font-size:34px;line-height:34px}
  .headline .bold{display:block;font-size:33px;line-height:38px;letter-spacing:-0.5px}
  .headline .accent{display:block;font-family:"Bebas Neue",sans-serif;font-weight:400;font-size:67px;line-height:62px;color:var(--yellow)}
  .tagline{left:50px;top:292px;font-size:19px;line-height:24px;font-weight:500}

  .illustration{left:72px;top:374px;width:260px;height:196px;border-radius:10px;
    background:linear-gradient(160deg,#d9dde2 0%,#8c949c 55%,rgba(40,40,40,0) 100%)}

  .pitch{left:50px;top:588px;font-family:"Poppins",sans-serif;font-weight:700;font-size:22px;line-height:31px}
  .pitch .hl{color:var(--yellow)}

  .banner{left:48px;top:726px;width:347px;height:32px;background:var(--yellow);border-radius:3px;
    font-family:"Bebas Neue",sans-serif;font-size:31px;line-height:34px;color:var(--ink);text-align:center;letter-spacing:1px}

  .benefits{left:48px;top:783px;width:300px;list-style:none;font-size:14.5px;line-height:18px}
  .benefits li{position:relative;padding-left:17px;margin-bottom:8px}
  .benefits li::before,.services li::before{content:"";position:absolute;left:0;top:5px;width:8px;height:8px;border-radius:50%;background:var(--yellow)}

  .cta{left:50px;top:1050px;font-family:"Poppins",sans-serif;font-weight:700;font-size:23px;line-height:29px;text-transform:uppercase}
  .cta .hl{color:var(--yellow)}
  .phone{left:50px;top:1116px;display:flex;align-items:center;gap:10px;font-family:"Montserrat",sans-serif;font-weight:800;font-size:33px;letter-spacing:4px}

  /* right column */
  .photo{left:434px;top:0;width:434px;height:436px;border-bottom-left-radius:26px;
    background:linear-gradient(135deg,var(--photo-a) 0%,var(--photo-b) 45%,var(--photo-c) 62%,var(--photo-b) 80%)}
  .photo-rule{left:446px;top:440px;width:422px;height:3px;background:var(--yellow);border-bottom-left-radius:10px}
  .tab{left:815px;top:395px;width:60px;height:96px;border-radius:10px;background:linear-gradient(180deg,#ffef1a,var(--yellow))}

  .services-title{left:434px;top:470px;font-family:"Bebas Neue",sans-serif;font-size:56px;line-height:52px;letter-spacing:5px;color:var(--yellow)}
  .services-sub{left:434px;top:532px;font-weight:700;font-size:15px}

  .services-panel{left:433px;top:571px;width:435px;height:474px;background:var(--yellow-bright);border-radius:40px 0 0 40px}
  .services{left:458px;top:604px;width:390px;list-style:none;color:var(--ink);font-weight:600;font-size:14px;line-height:17px}
  .services li{position:relative;padding-left:15px;margin-bottom:15px}
  .services li::before{background:var(--ink);top:4px}

  .email{left:434px;top:1093px;display:flex;align-items:center;gap:10px;font-size:16px}
  .web{left:434px;top:1128px;width:420px;white-space:nowrap;font-size:18px;letter-spacing:1.2px;font-weight:500}
  .web .hl{color:var(--yellow);font-weight:700}
</style>
</head>
<body>
<main class="flyer">
  <div class="abs brand">
    <span class="brand-name">BRIGHT LANE<br>BOOKKEEPING</span>
    <span class="brand-mark"></span>
  </div>

  <h1 class="abs headline">
    <span class="light">Virtual</span>
    <span class="bold">Bookkeeping for</span>
    <span class="accent">Small Business</span>
  </h1>
  <p class="abs tagline">Build Your Business by<br>Focusing on What You Love</p>

  <div class="abs illustration" role="img" aria-label="Illustration of a laptop showing a bookkeeping chart, with a calculator, notepad and pen"></div>

  <p class="abs pitch">Take charge of your<br>business and concentrate<br><span class="hl">on your strengths to<br>become its hero!</span></p>

  <div class="abs banner">Outsource your bookkeeping!</div>

  <ul class="abs benefits">
    <li>Take back your time</li>
    <li>Do more of what you love</li>
    <li>Focus on your strengths and what you<br>do best</li>
    <li>Confidently make business decisions</li>
    <li>Sail through tax time</li>
    <li>Save over the expense of a full-time<br>employee</li>
    <li>Pay yourself more</li>
    <li>Experience financial peace</li>
  </ul>

  <p class="abs cta">Request your<br><span class="hl">Free consultation</span></p>
  <div class="abs phone">
    <svg width="30" height="30" viewBox="0 0 30 30" aria-hidden="true"><circle cx="15" cy="15" r="14" fill="var(--yellow)"/><path d="M10 8c1-1 2 0 3 2s0 2-1 3c1 2 3 4 5 5 1-1 1-2 3-1s3 2 2 3c-1 2-3 3-6 1-3-2-5-4-7-7-1-3 0-5 1-6z" fill="var(--ink)"/></svg>
    <span>555-014-2277</span>
  </div>

  <div class="abs photo" role="img" aria-label="Photo of a stressed business owner working at a laptop in a bright office"></div>
  <div class="abs photo-rule"></div>
  <div class="abs tab"></div>

  <h2 class="abs services-title">Services</h2>
  <p class="abs services-sub">Bookkeeping Tailored to YOUR Business Needs</p>

  <div class="abs services-panel"></div>
  <ul class="abs services">
    <li>Catch-up and clean-up services</li>
    <li>Transaction importation and categorization</li>
    <li>Monthly reconciliation of all accounts,<br>including assets and loans.</li>
    <li>Monthly financial reports (Balance Sheet,</li>
    <li>Income Statement, Cash Flow)</li>
    <li>Monthly video conference</li>
    <li>Annual tax-prep package sent to your<br>preparer</li>
    <li>A/R &amp; A/P</li>
    <li>Payroll coordination</li>
    <li>1099s</li>
    <li>Bill pay and receipt management</li>
    <li>Budgeting</li>
  </ul>

  <div class="abs email">
    <svg width="18" height="18" viewBox="0 0 18 18" aria-hidden="true"><circle cx="9" cy="9" r="9" fill="var(--yellow)"/><rect x="4.5" y="5.5" width="9" height="7" rx="1" fill="var(--ink)"/><path d="M4.8 6l4.2 3.3L13.2 6" stroke="var(--yellow)" stroke-width="1" fill="none"/></svg>
    <span>maya@brightlanebookkeeping.example</span>
  </div>
  <p class="abs web">www.<span class="hl">brightlanebookkeeping</span>.example</p>
</main>
</body>
</html>
```